Business Card Design

I need business cards designed for a new company i have started that makes cakes, particularly themed kids cakes with a really modern design and I would like to have my business cards reflect this. I have attached some photos of cakes I have made and would like some to be used.

Industry/Entity Type

Business

Contact Information for Business Card

Business Name: Tarts and Treats by Maren
Mobile: 0492 815 063
email: maren@tartsandtreatsbymaren.example.au
Instagram: instagram.com/tartsandtreatsbymaren/
Facebook: fb.me/tartsandtreatsbymaren

Colors
e667a6
b768aa
3276b5

Requirements
Must have
• Business Name: Tarts and Treats by Maren
• Mobile: 0492 815 063
• email: maren@tartsandtreatsbymaren.example.au
• Instagram: instagram.com/tartsandtreatsbymaren/
• Facebook: fb.me/tartsandtreatsbymaren
Nice to have
• 2 to 3 pictures of my cakes

```html
<!DOCTYPE html>
<html lang="en">
<head>
<meta charset="utf-8">
<title>Tarts and Treats by Maren — Business Card</title>
<link rel="stylesheet" href="https://fonts.googleapis.com/css2?family=Open+Sans:wght@400;600;700&display=swap">
<style>
  :root {
    --pink: #e667a6;
    --pink-deep: #c9478a;
    --pink-light: #f08cbd;
    --plum: #b768aa;
    --ink-grey: #7a7a7a;
    --white: #ffffff;
    --backdrop: #ece8e4;
  }
  * { box-sizing: border-box; margin: 0; padding: 0; }
  html, body {
    width: 1200px; height: 843px; overflow: hidden;
    background: var(--backdrop);
    font-family: "Open Sans", sans-serif;
  }
  .canvas {
    width: 1200px; height: 843px;
    display: flex; flex-direction: column;
    align-items: center; justify-content: center; gap: 40px;
  }
  .card {
    position: relative;
    width: 620px; height: 354px;
    border-radius: 4px;
    overflow: hidden;
    box-shadow: 0 8px 24px rgba(0,0,0,.18);
  }
  .card-back {
    background: linear-gradient(100deg, var(--pink-deep) 0%, var(--pink) 35%, var(--pink-light) 50%, var(--pink) 65%, #b9407f 100%);
    display: flex; align-items: center; justify-content: center;
  }
  .brand-name {
    font-weight: 600;
    text-align: center;
    line-height: 1.15;
  }
  .card-back .brand-name { color: var(--white); font-size: 40px; }
  .brand-name .brand-by { display: block; font-size: .5em; letter-spacing: .12em; }
  .card-front { background: var(--white); }
  .card-front .swoosh { position: absolute; inset: 0; }
  .holder { position: absolute; left: 36px; top: 30px; }
  .holder-name {
    color: var(--pink); font-weight: 700; font-size: 20px; letter-spacing: .03em;
  }
  .holder-role { color: var(--ink-grey); font-size: 14px; }
  .card-front .brand-name {
    position: absolute; left: 130px; top: 96px; width: 320px;
    color: var(--pink); font-size: 34px;
  }
  .contact-list {
    position: absolute; right: 22px; bottom: 22px;
    list-style: none; text-align: right;
    color: var(--white); font-size: 14px; line-height: 22px;
  }
  .contact-list li { display: flex; justify-content: flex-end; align-items: center; gap: 8px; }
  .contact-icon { width: 13px; height: 13px; flex: none; }
</style>
</head>
<body>
<main class="canvas">
  <section class="card card-back" aria-label="Card back">
    <p class="brand-name">Tarts &amp; Treats<span class="brand-by">BY MAREN</span></p>
  </section>

  <section class="card card-front" aria-label="Card front">
    <svg class="swoosh" viewBox="0 0 620 354" preserveAspectRatio="none" aria-hidden="true">
      <defs>
        <linearGradient id="bandFill" x1="0" y1="0" x2="1" y2="0">
          <stop offset="0" stop-color="#c9478a"/>
          <stop offset=".3" stop-color="#e667a6"/>
          <stop offset=".42" stop-color="#f08cbd"/>
          <stop offset=".6" stop-color="#e667a6"/>
          <stop offset="1" stop-color="#b9407f"/>
        </linearGradient>
      </defs>
      <path d="M0 232 Q 300 290 620 118 L620 354 L0 354 Z" fill="url(#bandFill)"/>
      <path d="M0 224 Q 300 282 620 110" fill="none" stroke="#b768aa" stroke-width="5"/>
    </svg>

    <div class="holder">
      <p class="holder-name">ELENA HART</p>
      <p class="holder-role">CEO/Founder</p>
    </div>

    <p class="brand-name">Tarts &amp; Treats<span class="brand-by">BY MAREN</span></p>

    <ul class="contact-list">
      <li>0492 815 063
        <svg class="contact-icon" viewBox="0 0 13 13" role="img" aria-label="Mobile"><rect x="3" y="0.5" width="7" height="12" rx="1.5" fill="none" stroke="#fff" stroke-width="1.3"/><rect x="5.5" y="10" width="2" height="1.2" fill="#fff"/></svg></li>
      <li>tartsandtreatsbymaren
        <svg class="contact-icon" viewBox="0 0 13 13" role="img" aria-label="Photo gallery"><rect x="0.5" y="0.5" width="12" height="12" rx="2" fill="#fff"/></svg></li>
      <li>tartsandtreatsbymaren
        <svg class="contact-icon" viewBox="0 0 13 13" role="img" aria-label="Social page"><rect x="0.5" y="0.5" width="12" height="12" rx="2" fill="#fff"/></svg></li>
      <li>maren@tartsandtreatsbymaren.example.au
        <svg class="contact-icon" viewBox="0 0 13 13" role="img" aria-label="Email"><rect x="0.5" y="2.5" width="12" height="8" fill="#fff"/><path d="M0.5 2.5 L6.5 7 L12.5 2.5" fill="none" stroke="#e667a6" stroke-width="1"/></svg></li>
    </ul>
  </section>
</main>
</body>
</html>
```